Redesign of business card for Cedar Ridge Mechanical

We are looking for a new design for our business cards for Cedar Ridge Mechanical. We are a plumbing & HVAC construction company, operating on the West Coast of Canada and USA. Logo attached.
Industry/Entity Type
Construction - Plumbing & HVAC
Contact Information for Business Card
Name, address, phone numbers, email, website address
Look and feel
Each slider illustrates characteristics of the customer's brand and the style your logo design should communicate.

```html
<!DOCTYPE html>
<html lang="en">
<head>
<meta charset="utf-8">
<title>Cedar Ridge Mechanical — Business Card</title>
<link rel="stylesheet" href="https://fonts.googleapis.com/css2?family=Oswald:wght@500&family=Montserrat:wght@400;700&display=swap">
<style>
  :root {
    --backdrop: #8c7b63;
    --card: #2b2b2b;
    --ink: #ffffff;
    --ink-soft: #e6e6e6;
    --mark-ink: #0d0d0d;
  }
  * { margin: 0; padding: 0; box-sizing: border-box; }
  html, body { width: 900px; height: 1200px; overflow: hidden; }
  body {
    position: relative;
    background: var(--backdrop);
    font-family: "Montserrat", Arial, sans-serif;
    color: var(--ink);
  }
  .card {
    position: absolute;
    width: 742px;
    height: 442px;
    background: var(--card);
    border-radius: 22px;
  }
  .card-front { left: 80px; top: 130px; }
  .card-back { left: 79px; top: 637px; }

  .company-name {
    position: absolute;
    left: 35px;
    top: 48px;
    font-family: "Oswald", "Arial Narrow", sans-serif;
    font-weight: 500;
    font-size: 33px;
    letter-spacing: 1.5px;
    text-transform: uppercase;
  }
  .person {
    position: absolute;
    right: 56px;
    top: 36px;
    text-align: right;
  }
  .person-name { font-weight: 700; font-size: 25px; line-height: 1.2; }
  .person-title { font-size: 15.5px; color: var(--ink-soft); margin-top: 2px; }

  .address {
    position: absolute;
    left: 35px;
    top: 243px;
    font-size: 16px;
    line-height: 20px;
    color: var(--ink-soft);
  }
  .contact-list {
    position: absolute;
    left: 33px;
    top: 323px;
    list-style: none;
  }
  .contact-item {
    display: flex;
    align-items: center;
    height: 30.5px;
    font-size: 15.5px;
    color: var(--ink-soft);
  }
  .contact-icon { width: 16px; height: 16px; margin-right: 9px; fill: var(--ink); }

  .brand-mark-front {
    position: absolute;
    right: 48px;
    bottom: 58px;
    width: 300px;
    text-align: center;
    font-family: "Oswald", "Arial Narrow", sans-serif;
    font-weight: 500;
    font-size: 30px;
    line-height: 1.15;
    letter-spacing: 1.5px;
    text-transform: uppercase;
    color: var(--mark-ink);
  }

  .brand-lockup {
    position: absolute;
    left: 0; right: 0;
    top: 190px;
    display: flex;
    justify-content: center;
    align-items: center;
    gap: 18px;
  }
  .brand-square { width: 34px; height: 34px; background: var(--ink); }
  .brand-name {
    font-family: "Oswald", "Arial Narrow", sans-serif;
    font-weight: 500;
    font-size: 40px;
    letter-spacing: 2px;
    text-transform: uppercase;
    color: var(--ink);
  }
</style>
</head>
<body>

  <section class="card card-front">
    <h1 class="company-name">Cedar Ridge Mechanical</h1>
    <div class="person">
      <p class="person-name">Daniel Hart</p>
      <p class="person-title">Managing Director</p>
    </div>
    <address class="address" style="font-style:normal">48 Timber Lane<br>Fairview, OR 97024</address>
    <ul class="contact-list">
      <li class="contact-item">
        <svg class="contact-icon" viewBox="0 0 24 24" aria-hidden="true"><path d="M6.6 10.8a15.1 15.1 0 0 0 6.6 6.6l2.2-2.2a1 1 0 0 1 1-.25 11.4 11.4 0 0 0 3.6.57 1 1 0 0 1 1 1V20a1 1 0 0 1-1 1A17 17 0 0 1 3 4a1 1 0 0 1 1-1h3.5a1 1 0 0 1 1 1c0 1.25.2 2.45.57 3.6a1 1 0 0 1-.25 1z"/></svg>
        555.214.7730
      </li>
      <li class="contact-item">
        <svg class="contact-icon" viewBox="0 0 24 24" aria-hidden="true"><path d="M3 6h18v12H3z" opacity="0"/><path d="M3 6l9 6 9-6v12H3z"/><path d="M3 5h18l-9 6z"/></svg>
        info@cedarridgemechanical.com
      </li>
      <li class="contact-item">
        <svg class="contact-icon" viewBox="0 0 24 24" aria-hidden="true"><circle cx="12" cy="12" r="10"/><path d="M2 12h20M12 2c3 3 3 17 0 20M12 2c-3 3-3 17 0 20" stroke="#2b2b2b" stroke-width="1.6" fill="none"/></svg>
        www.cedarridgemechanical.com
      </li>
    </ul>
    <p class="brand-mark-front">Cedar Ridge<br>Mechanical</p>
  </section>

  <section class="card card-back">
    <div class="brand-lockup">
      <span class="brand-square" aria-hidden="true"></span>
      <p class="brand-name">Cedar Ridge Mechanical</p>
    </div>
  </section>

</body>
</html>
```